Bright Harbor Web Design & Marketing

Will award a 2nd place prize of $100.00 if someone can come up with a logo to match this design!
Updates

Okay, I'm really looking to see some better designs here. What do you think will bring the best designs out? Please remember with all future submissions I'm looking for a cartoon style / illustrator style website. I'm not sure what the technical term is for it, so I uploaded some images in the brief.

Target Market(s)

Small Business Owners

Industry/Entity Type

Marketing

Logo Text

BrightHarbor.com

Number of Pages Required

1 page

Colors

Designer to choose colors to be used in the design.

Requirements
Must have
• Logo should say BrightHarbor.com I would like more than just a text logo. I want some sort of cool custom graphic / icon with it that will look nice on shirts/hats/etc

```html
<!DOCTYPE html>
<html lang="en">
<head>
<meta charset="utf-8">
<title>Bright Harbor Web Design &amp; Marketing</title>
<link rel="stylesheet" href="https://fonts.googleapis.com/css2?family=Cinzel:wght@400;700&family=Tinos:wght@400;700&family=Open+Sans:wght@400;600;700&display=swap">
<style>
:root{
  --teal:#1fb493;
  --teal-dark:#17977b;
  --navy:#0b3a51;
  --navy-deep:#082c3e;
  --ink:#222;
  --muted:#555;
  --grey-bg:#f2f2f2;
  --line:#dcdcdc;
  --white:#fff;
}
*{box-sizing:border-box;margin:0;padding:0}
html,body{width:1200px;height:4009px;overflow:hidden;background:var(--white)}
body{font-family:"Tinos",serif;color:var(--ink);position:relative}
section,header,footer,nav{position:absolute;left:0;width:1200px}
.abs{position:absolute}
.heading{font-family:"Cinzel",serif;font-weight:400;text-align:center;color:var(--navy);font-size:34px;letter-spacing:1px}
.heading b{font-weight:400;color:var(--teal)}
.lead{font-size:14px;line-height:21px;color:var(--ink);text-align:center;width:860px;margin:0 auto}
.pill{display:inline-flex;align-items:center;gap:8px;background:var(--navy);color:var(--white);font-family:"Open Sans",sans-serif;font-weight:600;font-size:15px;padding:7px 20px 7px 10px;border-radius:18px;white-space:nowrap}
.pill .dot{width:20px;height:20px;border-radius:50%;background:var(--teal)}

/* header */
.site-header{top:0;height:85px}
.brand{left:147px;top:14px;display:flex;align-items:center;gap:12px}
.brand .mark{width:50px;height:50px;border-radius:50%;background:var(--teal)}
.brand .name{font-family:"Cinzel",serif;font-weight:700;font-size:30px;color:var(--navy);white-space:nowrap}
.phone{left:878px;top:26px;display:flex;align-items:center;gap:8px;font-family:"Open Sans",sans-serif;font-weight:700;font-size:26px;color:var(--navy)}
.main-nav{top:85px;height:35px;background:var(--teal)}
.main-nav a{position:absolute;font-family:"Cinzel",serif;font-size:15px;color:var(--white);text-decoration:none;top:0;height:35px;line-height:35px;white-space:nowrap}
.main-nav a.active{background:var(--navy);padding:0 22px}

/* hero */
.hero{top:120px;height:473px;background:radial-gradient(ellipse at 60% 45%,#2a6fb0 0%,#123f78 45%,#071d3d 100%);text-align:center;color:var(--white)}
.hero h1{position:absolute;top:160px;width:100%;font-family:"Open Sans",sans-serif;font-weight:700;font-size:28px}
.hero p{position:absolute;top:212px;width:100%;font-family:"Open Sans",sans-serif;font-size:21px}
.hero .pill{position:absolute;top:270px;left:518px;background:transparent}
.hero .arrow{position:absolute;top:228px;width:22px;height:22px;background:#555;opacity:.8}

/* about */
.about{top:593px;height:310px}
.about h2{position:absolute;left:142px;top:40px;width:530px;white-space:nowrap;font-family:"Cinzel",serif;font-weight:400;font-size:24px;color:var(--teal)}
.about .text{position:absolute;left:142px;top:98px;width:525px;font-size:14px;line-height:22px}
.about .text p+p{margin-top:14px}
.video{left:690px;top:55px;width:335px;height:205px;background:linear-gradient(#3b3b3b,#2a2a2a);border-radius:8px}
.video .screen{position:absolute;left:16px;top:14px;right:16px;bottom:22px;background:#ededed;display:flex;align-items:center;justify-content:center}
.video .play{width:42px;height:42px;border-radius:50%;background:#222;display:flex;align-items:center;justify-content:center}

/* services */
.services{top:903px;height:553px;background:var(--grey-bg)}
.services .heading{position:absolute;top:50px;width:100%}
.services .lead{position:absolute;top:105px;left:170px}
.svc-menu{left:142px;top:185px;width:248px;list-style:none}
.svc-menu li{height:27px;margin-bottom:2px;background:var(--navy);color:var(--white);font-family:"Open Sans",sans-serif;font-size:11px;display:flex;align-items:center;gap:8px;padding-left:8px;white-space:nowrap}
.svc-menu li::before{content:"";width:12px;height:12px;background:var(--teal);border-radius:2px}
.svc-menu li.active{background:var(--teal)}
.svc-menu li.active::before{background:var(--white)}
.svc-art{left:415px;top:232px;width:120px;height:120px;background:linear-gradient(#d6d6d6,#c4c4c4);border-radius:6px}
.svc-detail{left:555px;top:206px;width:470px}
.svc-detail h3{font-family:"Open Sans",sans-serif;font-weight:700;font-size:15px;text-decoration:underline;color:var(--ink);margin-bottom:12px}
.svc-detail li{list-style:none;display:flex;gap:10px;font-size:12px;line-height:17px;margin-bottom:11px}
.svc-detail li svg{flex:none;margin-top:1px}
.svc-detail h4{font-family:"Cinzel",serif;font-weight:700;color:var(--teal);font-size:19px;margin:10px 0 12px 20px}

/* banner */
.banner{top:1456px;height:222px;text-align:center}
.banner h2{position:absolute;top:44px;width:100%;font-family:"Cinzel",serif;font-weight:700;color:var(--teal);font-size:38px}
.banner p{position:absolute;top:98px;width:100%;font-size:21px;line-height:27px;color:var(--ink)}
.banner .pill{position:absolute;top:158px;left:476px;font-size:16px}

/* pricing */
.pricing{top:1678px;height:660px;background:linear-gradient(90deg,#0b3f53,#0e4b61 50%,#0b3f53)}
.pricing .heading{position:absolute;top:46px;width:100%;color:var(--white)}
.floor{left:0;top:487px;width:1200px;height:173px;background:linear-gradient(#b47b46,#d9a46e)}
.plan{top:147px;width:208px;height:446px;background:var(--white);border-top:4px solid var(--teal);box-shadow:0 6px 12px rgba(0,0,0,.3);text-align:center}
.plan .ic{width:52px;height:52px;border-radius:50%;border:3px solid var(--teal);margin:22px auto 0;display:flex;align-items:center;justify-content:center}
.plan .ic i{width:22px;height:22px;border-radius:50%;background:var(--navy)}
.plan.gold .ic i{background:#f0a93b}
.plan h3{font-family:"Open Sans",sans-serif;font-weight:600;font-size:17px;margin-top:16px}
.plan .band{margin-top:18px;background:#f4f4f4;padding:10px 0 14px;border-top:1px solid var(--line)}
.plan small{font-size:12px;color:var(--muted)}
.plan .price{font-family:"Open Sans",sans-serif;font-size:42px;color:var(--ink)}
.plan .price sup,.plan .price span{font-size:15px}
.plan ul{list-style:none;text-align:left;padding:14px 18px 0;font-size:12px;background:#f4f4f4;height:120px}
.plan ul li{margin-bottom:9px}
.plan ul li::before{content:"› ";color:var(--muted)}
.plan .go{display:inline-block;margin-top:14px;background:var(--teal);color:var(--white);font-family:"Open Sans",sans-serif;font-weight:600;font-size:13px;padding:6px 18px}
.plan.basic .go{background:var(--navy)}
.plan .more{display:block;margin-top:10px;font-family:"Open Sans",sans-serif;font-size:10px}

/* clients */
.clients{top:2338px;height:254px}
.clients .heading{position:absolute;top:56px;width:100%}
.clients .lead{position:absolute;top:106px;left:170px}
.client-row{top:172px;left:105px;width:990px;display:flex;justify-content:space-between;align-items:center}
.client{display:flex;align-items:center;gap:6px;font-family:"Open Sans",sans-serif;font-weight:700;font-size:16px;color:#333}
.client i{width:14px;height:14px;border-radius:50%;background:#333}
.client-row .nav-arrow{font-family:"Open Sans",sans-serif;font-size:26px;color:#999}

/* why */
.why{top:2592px;height:502px;background:var(--grey-bg)}
.why .heading{position:absolute;top:50px;width:100%}
.why .lead{position:absolute;top:102px;left:170px}
.perk{top:152px;width:148px;height:168px;background:var(--white);box-shadow:0 2px 6px rgba(0,0,0,.12);text-align:center}
.perk .art{width:96px;height:84px;margin:16px auto 12px;background:linear-gradient(#cfe9e2,#b5d9cf);border-radius:6px}
.perk p{font-family:"Open Sans",sans-serif;font-size:11px;line-height:14px;padding:0 8px}
.perk-detail{left:150px;top:336px;width:900px;height:145px;background:var(--white);border-top:2px solid var(--teal);padding:14px 10px;font-size:13px;line-height:20px}
.perk-detail h4{font-family:"Open Sans",sans-serif;font-weight:600;font-size:15px;color:var(--navy);margin-bottom:8px}

/* team */
.team{top:3094px;height:358px}
.team .heading{position:absolute;top:50px;width:100%}
.team .lead{position:absolute;top:100px;left:170px}
.member{top:155px;width:450px;height:166px;border:1px solid var(--line);padding:16px}
.member .photo{position:absolute;left:16px;top:14px;width:68px;height:68px;background:linear-gradient(#9aa7b2,#6d7b88)}
.member h4{margin-left:90px;margin-top:18px;font-family:"Open Sans",sans-serif;font-weight:700;font-size:14px;color:var(--navy)}
.member h5{margin-left:90px;font-family:"Open Sans",sans-serif;font-weight:400;font-size:12px;color:var(--teal)}
.member p{margin-top:26px;font-size:12.5px;line-height:18px}
.team .side{top:235px;font-family:"Open Sans",sans-serif;font-size:26px;color:#aaa}

/* inquiry */
.inquiry{top:3452px;height:404px}
.tabs{left:500px;top:16px;display:flex;gap:22px}
.tabs i{width:36px;height:36px;background:var(--navy)}
.tabs i+i{background:var(--teal)}
.desk{left:0;top:20px;width:450px;height:370px;background:linear-gradient(135deg,#f1f1f1,#d4d6d8)}
.inquiry h2{position:absolute;left:500px;top:58px;font-family:"Cinzel",serif;font-weight:700;font-size:33px;color:var(--teal);white-space:nowrap}
.field{font-family:"Open Sans",sans-serif;font-size:11px;color:#444;border-bottom:1px solid var(--line);height:24px}
.area{left:500px;top:242px;width:515px;height:72px;border:1px solid var(--line)}
.submit{left:500px;top:336px;width:90px;height:32px;background:var(--teal);color:var(--white);font-family:"Open Sans",sans-serif;font-size:12px;font-weight:600;text-align:center;line-height:32px}

/* footer */
.site-footer{top:3856px;height:153px;background:var(--navy-deep);color:var(--white);font-family:"Open Sans",sans-serif}
.contact{top:40px;display:flex;gap:14px;font-size:11px;line-height:15px}
.contact .ring{width:44px;height:44px;border-radius:50%;border:2px solid var(--teal);display:flex;align-items:center;justify-content:center;flex:none}
.contact b{font-weight:700}
.copy{left:222px;top:117px;font-size:10px}
.social{left:885px;top:110px;display:flex;gap:8px}
.social i{width:20px;height:20px;border-radius:50%;border:1px solid #8aa}
</style>
</head>
<body>

<header class="site-header">
  <div class="brand abs"><span class="mark"></span><span class="name">Bright Harbor Web Design</span></div>
  <div class="phone abs">
    <svg width="26" height="26" viewBox="0 0 24 24"><circle cx="12" cy="12" r="11" fill="none" stroke="#1fb493" stroke-width="2"/><path d="M8 6l2 0 1 3-1.5 1a7 7 0 0 0 3.5 3.5l1-1.5 3 1 0 2a2 2 0 0 1-2 2A9 9 0 0 1 6 8a2 2 0 0 1 2-2z" fill="#1fb493"/></svg>
    123-456-7890
  </div>
</header>

<nav class="main-nav">
  <a class="active" href="#" style="left:152px">HOME</a>
  <a href="#" style="left:312px">SERVICES &amp; PRICING</a>
  <a href="#" style="left:578px">OUR TEAM</a>
  <a href="#" style="left:764px">CLIENTS</a>
  <a href="#" style="left:937px">CONTACT US</a>
</nav>

<section class="hero" role="img" aria-label="Dark blue network of connected points background">
  <span class="arrow" style="left:0"></span>
  <span class="arrow" style="right:0"></span>
  <h1>Bright Harbor Web Design</h1>
  <p>The Design &amp; Marketing Team That Always Puts Trust &amp; Loyalty Before Profits</p>
  <span class="pill"><span class="dot"></span>Call Us Today</span>
</section>

<section class="about">
  <h2>About Bright Harbor Web Design</h2>
  <div class="text">
    <p>We believe that honesty and integrity come before personal profits. We are a family owned and operated company. Our parents raised us to take care of each other and that's exactly what we've done. We treat each of our clients with the same loyalty and respect that we give each other.</p>
    <p>We are not looking to have hundreds and hundreds of clients. We are looking to expand our family with a handful of like-minded individuals. Companies who take pride in their work and their customers. We want to build mutually beneficial, lucrative, and long term partnerships.</p>
  </div>
  <div class="video abs" role="img" aria-label="Laptop showing the company introduction video">
    <div class="screen">
      <span class="play"><svg width="16" height="16" viewBox="0 0 16 16"><path d="M4 2l10 6-10 6z" fill="#fff"/></svg></span>
    </div>
  </div>
</section>

<section class="services">
  <h2 class="heading"><b>Services</b> We Provide</h2>
  <p class="lead">Lorem ipsum dolor sit amet, consectetuer adipiscing elit, sed diam nonummy nibh euismod tincidunt ut laoreet dolore magna aliquam erat volutpat. Ut wisi enim ad minim veniam, quis nostrud exerci.</p>
  <ul class="svc-menu abs">
    <li class="active">Website Design &amp; Management</li>
    <li>Logo Design &amp; Branding Materials</li>
    <li>Online Store Design &amp; Management</li>
    <li>Local Seo Management</li>
    <li>Search Engine Optimization</li>
    <li>Social Media Marketing</li>
    <li>Marketing Material &amp; Print Design</li>
    <li>Reputation Management</li>
    <li>Outsourcing Management</li>
    <li>Consulting Service</li>
  </ul>
  <div class="svc-art abs" role="img" aria-label="Illustration of a monitor and stylus"></div>
  <div class="svc-detail abs">
    <h3>Website Design &amp; Management</h3>
    <ul>
      <li><svg width="14" height="14" viewBox="0 0 14 14"><rect x=".5" y=".5" width="13" height="13" fill="none" stroke="#0b3a51"/><path d="M3 7l3 3 5-6" stroke="#0b3a51" stroke-width="1.8" fill="none"/></svg>Lorem dolor sit amet, consectetuer adipiscing elit, sed diam nonummy nibh euismod</li>
      <li><svg width="14" height="14" viewBox="0 0 14 14"><rect x=".5" y=".5" width="13" height="13" fill="none" stroke="#0b3a51"/><path d="M3 7l3 3 5-6" stroke="#0b3a51" stroke-width="1.8" fill="none"/></svg>Lorem dolor sit amet, consectetuer adipiscing</li>
      <li><svg width="14" height="14" viewBox="0 0 14 14"><rect x=".5" y=".5" width="13" height="13" fill="none" stroke="#0b3a51"/><path d="M3 7l3 3 5-6" stroke="#0b3a51" stroke-width="1.8" fill="none"/></svg>Lorem dolor sit amet, consectetuer adipiscing elit, sed diam nonummy nibh euismod</li>
      <li><svg width="14" height="14" viewBox="0 0 14 14"><rect x=".5" y=".5" width="13" height="13" fill="none" stroke="#0b3a51"/><path d="M3 7l3 3 5-6" stroke="#0b3a51" stroke-width="1.8" fill="none"/></svg>Lorem dolor sit amet, consectetuer adipiscing elit, sed diam nonummy nibh euismod.ornare dolor sit amet.</li>
    </ul>
    <h4>We Have Answers</h4>
    <span class="pill"><span class="dot"></span>Call Us Today To Avail The Service</span>
  </div>
</section>

<section class="banner">
  <h2>Lorem Ipsum Dolor Sit Amet Consectetuer</h2>
  <p>Lorem ipsum dolor sit amet consectetuer adipiscing elit sed diam the nonummy nibh sit amet consectetuer<br>adipiscing elit sed consectetuer.</p>
  <span class="pill"><span class="dot"></span>Call Us Today</span>
</section>

<section class="pricing">
  <h2 class="heading">Our Pricing</h2>
  <div class="floor abs" role="img" aria-label="Wooden floor boards"></div>

  <div class="plan basic abs" style="left:160px">
    <div class="ic"><i></i></div><h3>Basic Plan</h3>
    <div class="band"><small>Starting from</small><div class="price"><sup>$</sup>52<span>.95</span></div></div>
    <ul><li>Lorem Ipsum Dolor Ipsum</li><li>Lorem Ipsum Dolor</li><li>Lorem Ipsum Dolor Ipsum</li><li>Lorem Ipsum Dolor</li></ul>
    <span class="go">Get Started →</span><span class="more">More Information ▪</span>
  </div>
  <div class="plan abs" style="left:393px;top:137px">
    <div class="ic"><i></i></div><h3>Standard Plan</h3>
    <div class="band"><small>Starting from</small><div class="price"><sup>$</sup>114<span>.00</span></div></div>
    <ul><li>Lorem Ipsum Dolor Ipsum</li><li>Lorem Ipsum Dolor</li><li>Lorem Ipsum Dolor Ipsum</li><li>Lorem Ipsum Dolor</li></ul>
    <span class="go">Get Started →</span><span class="more">More Information ▪</span>
  </div>
  <div class="plan gold abs" style="left:623px">
    <div class="ic"><i></i></div><h3>Gold Plan</h3>
    <div class="band"><small>Starting from</small><div class="price"><sup>$</sup>200<span>.95</span></div></div>
    <ul><li>Lorem Ipsum Dolor Ipsum</li><li>Lorem Ipsum Dolor</li><li>Lorem Ipsum Dolor Ipsum</li><li>Lorem Ipsum Dolor</li></ul>
    <span class="go">Get Started →</span><span class="more">More Information ▪</span>
  </div>
  <div class="plan abs" style="left:855px">
    <div class="ic"><i></i></div><h3>Platinum Plan</h3>
    <div class="band"><small>Starting from</small><div class="price"><sup>$</sup>490<span>.00</span></div></div>
    <ul><li>Lorem Ipsum Dolor Ipsum</li><li>Lorem Ipsum Dolor</li><li>Lorem Ipsum Dolor Ipsum</li><li>Lorem Ipsum Dolor</li></ul>
    <span class="go">Get Started →</span><span class="more">More Information ▪</span>
  </div>
</section>

<section class="clients">
  <h2 class="heading">Our <b>Valuable</b> Clients</h2>
  <p class="lead">Lorem ipsum dolor sit amet, consectetuer adipiscing elit, sed diam nonummy nibh euismod tincidunt ut laoreet dolore magna aliquam erat volutpat. Ut wisi enim ad minim veniam, quis nostrud exerci.</p>
  <div class="client-row abs">
    <span class="nav-arrow">‹</span>
    <span class="client"><i></i>Ridgeway</span>
    <span class="client">Cobalt</span>
    <span class="client">Cobalt</span>
    <span class="client">Northfield</span>
    <span class="client"><i></i>Ridgeway</span>
    <span class="client">Meridian</span>
    <span class="client">Arcline</span>
    <span class="client">Arcline</span>
    <span class="nav-arrow">›</span>
  </div>
</section>

<section class="why">
  <h2 class="heading"><b>Why</b> Choose Us</h2>
  <p class="lead">Lorem ipsum dolor sit amet, consectetuer adipiscing elit, sed diam nonummy nibh euismod tincidunt ut laoreet dolore magna aliquam erat volutpat. Ut wisi enim ad minim veniam, quis nostrud exerci.</p>
  <div class="perk abs" style="left:155px"><div class="art" role="img" aria-label="Hand holding a coin"></div><p>100% Risk Free Investment</p></div>
  <div class="perk abs" style="left:355px"><div class="art" role="img" aria-label="Hand holding a loyalty card"></div><p>Customer Loyalty Program</p></div>
  <div class="perk abs" style="left:526px"><div class="art" role="img" aria-label="Clock showing round-the-clock support"></div><p>24/7 U.S Based Customer Support</p></div>
  <div class="perk abs" style="left:704px"><div class="art" role="img" aria-label="Support agent at a screen"></div><p>Unmatched Personal Service</p></div>
  <div class="perk abs" style="left:890px"><div class="art" role="img" aria-label="Various payment methods"></div><p>Multiple Payment Options Available</p></div>
  <div class="perk-detail abs">
    <h4>Unmatched Personal Service</h4>
    <p>Do you need us to come to your office to help train staff on the management of your new website, content management system, or computer software?<br>That's not a problem.<br>We welcome to you and provide hands on training.</p>
  </div>
</section>

<section class="team">
  <h2 class="heading">Our <b>Team</b></h2>
  <p class="lead">Lorem ipsum dolor sit amet, consectetuer adipiscing elit, sed diam nonummy nibh euismod tincidunt ut laoreet dolore magna aliquam erat volutpat. Ut wisi enim ad minim veniam, quis nostrud exerci.</p>
  <span class="side abs" style="left:112px">‹</span>
  <span class="side abs" style="left:1070px">›</span>
  <div class="member abs" style="left:155px">
    <div class="photo" role="img" aria-label="Portrait of the chief executive officer"></div>
    <h4>DANIEL WHITCOMBE</h4><h5>Chief Executive Officer</h5>
    <p>Lorem ipsum dolor sit amet, consectetuer adipiscing elit, sed diam nonummy nibh euismod tincidunt ut laoreet dolore magna aliquam...[+]</p>
  </div>
  <div class="member abs" style="left:620px">
    <div class="photo" role="img" aria-label="Portrait of the chief operations officer"></div>
    <h4>OWEN HARTLEY</h4><h5>Chief Operations Officer</h5>
    <p>Lorem ipsum dolor sit amet, consectetuer adipiscing elit, sed diam nonummy nibh euismod tincidunt ut laoreet dolore magna aliquam...[+]</p>
  </div>
</section>

<section class="inquiry">
  <div class="desk abs" role="img" aria-label="Person working on a laptop at a white desk"></div>
  <div class="tabs abs"><i></i><i></i></div>
  <h2>Quick Inquiry</h2>
  <div class="field abs" style="left:500px;top:120px;width:245px">First Name</div>
  <div class="field abs" style="left:770px;top:120px;width:245px">Last Name</div>
  <div class="field abs" style="left:500px;top:168px;width:245px">Email</div>
  <div class="field abs" style="left:770px;top:168px;width:245px">Phone Number</div>
  <div class="field abs" style="left:500px;top:216px;width:515px;border:none">Details About Your Enquiry</div>
  <div class="area abs"></div>
  <div class="submit abs">SUBMIT</div>
</section>

<footer class="site-footer">
  <div class="contact abs" style="left:212px">
    <span class="ring"><svg width="18" height="20" viewBox="0 0 18 22"><path d="M9 1a7 7 0 0 0-7 7c0 5 7 13 7 13s7-8 7-13a7 7 0 0 0-7-7z" fill="none" stroke="#1fb493" stroke-width="2"/><circle cx="9" cy="8" r="2.5" fill="#1fb493"/></svg></span>
    <div><b>Bright Harbor Web Design</b><br>Street Name, City Name<br>State Zip code</div>
  </div>
  <div class="contact abs" style="left:528px">
    <span class="ring"><svg width="18" height="18" viewBox="0 0 24 24"><path d="M6 3l3 0 2 5-2 1.5a10 10 0 0 0 5.5 5.5l1.5-2 5 2 0 3a2 2 0 0 1-2 2A16 16 0 0 1 4 5a2 2 0 0 1 2-2z" fill="#1fb493"/></svg></span>
    <div><b>Phone:</b><br>+012 3456 789</div>
  </div>
  <div class="contact abs" style="left:790px">
    <span class="ring"><svg width="20" height="14" viewBox="0 0 20 14"><rect x="1" y="1" width="18" height="12" fill="none" stroke="#1fb493" stroke-width="1.6"/><path d="M1 1l9 7 9-7" fill="none" stroke="#1fb493" stroke-width="1.6"/></svg></span>
    <div><b>Email:</b><br>inquiry@brightharbor.com</div>
  </div>
  <div class="copy abs">Copyright © 2017 BRIGHT HARBOR WEB DESIGN. All Rights Reserved.</div>
  <div class="social abs"><i></i><i></i><i></i><i></i><i></i></div>
</footer>

</body>
</html>
```